9x12 Business Brochure, 3 fold, for Internet Marketing Company

I'd like to have a brochure designed for my Internet marketing company. I have the content all ready, 10 Internet Marketing Myths, which you can see here: http://www.brisklanternstudio.example/usual-web-promotion-fables/. I'm looking for something creative and business to business. The company is all about Internet marketing. I like the "http://" header I use at our website. People like it too and identify with it. Audience is business owners 35 to 55 years old. I use blue at my website. I *think* I would like the cover page (front page) to open with some attention grabbing text, that basically takes most of the front page of the brochure. It would probably say: "I Can Help You Get BETTER RESULTS from Your Website, More Traffic, TOP RANKINGS at Quorble, More Leads and MORE SALES. But first you'll have to avoid these common Internet marketing myths..." The inside pages would have the content from above (the 10 myths). The back page would have testimonials that I can provide. And the inside folded in page (or what I call the inside folded in page) would have a list of services. I think I want the dimensions 12x9 which is a larger sized, three-fold brochure.

Target Market(s)

I use this brochure to send to business owners and managers to show them I know what I'm talking about and and expert. See attachment for content.

Industry/Entity Type

Marketing

Requirements
Should not have
• No clipart. Probably not illustrations. Photos. The "http://" used at the site is something people "connect" with and get that this is about Internet marketing.

```html
<!DOCTYPE html>
<html lang="en">
<head>
<meta charset="utf-8">
<title>Common Internet Marketing Myths</title>
<link href="https://fonts.googleapis.com/css2?family=Waiting+for+the+Sunrise&display=swap" rel="stylesheet">
<style>
  :root {
    --paper: #ffffff;
    --ink: #3a3a3a;
    --heading-blue: #1d4f7c;
    --title-grey: #5a5a5a;
    --title-shadow: rgba(0, 0, 0, 0.22);
  }
  html, body {
    margin: 0;
    padding: 0;
    overflow: hidden;
    background: var(--paper);
  }
  .brochure-panel {
    position: relative;
    width: 1200px;
    height: 900px;
    overflow: hidden;
    background: var(--paper);
  }
  .panel-title {
    position: absolute;
    left: 22px;
    top: 30px;
    width: 368px;
    margin: 0;
    text-align: center;
    font-family: "Waiting for the Sunrise", cursive;
    font-weight: 400;
    font-size: 40px;
    line-height: 46px;
    color: var(--title-grey);
    text-shadow: 2px 3px 3px var(--title-shadow);
  }
  .myth {
    position: absolute;
    margin: 0;
  }
  .col-one { left: 22px; width: 368px; }
  .col-two { left: 418px; width: 367px; }
  .col-three { left: 810px; width: 368px; }
  .myth-heading {
    margin: 0 0 4px;
    font-family: "Waiting for the Sunrise", cursive;
    font-weight: 400;
    font-size: 23px;
    line-height: 26px;
    color: var(--heading-blue);
  }
  .myth-heading .line-end {
    display: block;
    text-align: right;
  }
  .myth-body {
    margin: 0;
    font-family: Arial, Helvetica, sans-serif;
    font-weight: 700;
    font-size: 14.4px;
    line-height: 20.2px;
    color: var(--ink);
    text-align: justify;
  }
</style>
</head>
<body>
<main class="brochure-panel">
  <h1 class="panel-title">Common Internet<br>Marketing Myths...</h1>

  <section class="myth col-one" style="top:166px">
    <h2 class="myth-heading">Myth # 1 If You Build It They Will Come</h2>
    <p class="myth-body">Building a website is no guarantee of online success. If you build it, don't assume people will find it. This is a guaranteed losing strategy. For your Internet marketing to succeed your website will need quality traffic (i.e. visitor sessions) and then convert those visitors into phone calls and online inquiries.</p>
  </section>

  <section class="myth col-one" style="top:366px">
    <h2 class="myth-heading">Myth # 2 Search Engines Are All You'll Need</h2>
    <p class="myth-body">It is a very common misconception, and costly mistake, to think that search engines and organic search engine positioning is all you need for online success. While a top ranked website is a very valuable asset, and it can drive a lot of qualified traffic to your website, it can take months, or years, to achieve that positioning — if you can get it at all. You'll need a multi-pronged approach to building traffic, including buying advertising, pay-per-click advertising (PPC), integration of your offline marketing with your online marketing, blogging, social media, and of course, search engine optimization (SEO).</p>
  </section>

  <section class="myth col-one" style="top:686px">
    <h2 class="myth-heading">Myth # 3 All Traffic is Good</h2>
    <p class="myth-body">Not true! To get real results from your website, inquiries, phone calls, and sales, you'll need to find and attract QUALIFIED traffic – people who are actually getting married and who are ready to purchase your products and services.</p>
  </section>

  <section class="myth col-two" style="top:40px">
    <h2 class="myth-heading">Myth # 4 Hits Are A Good Measure of Success</h2>
    <p class="myth-body">Wrong! If you are measuring “hits” you're not even in the game. A “hit” is a technical term that describes activity on a hosting server. Unfortunately, most webmasters use this term casually and it is interpreted to mean you have lots of traffic. Hits are not real people. Real people who visit your website are logged as “visitor sessions.”</p>
  </section>

  <section class="myth col-two" style="top:240px">
    <h2 class="myth-heading">Myth # 5 You Can Do This All Yourself</h2>
    <p class="myth-body">If you are in any competitive category of products or services, or in a geographically competitive marketplace, the chances that you can build a website, develop the traffic, and manage your ongoing online marketing ALL BY YOURSELF are less than one in ten. Put another way, DIY has a 90% chance of FAILURE.</p>
  </section>

  <section class="myth col-two" style="top:442px">
    <h2 class="myth-heading">Myth # 6 It's Easy to Get Traffic <span class="line-end">From Search Engines</span></h2>
    <p class="myth-body">In today's competitive marketplace it is more difficult than ever to get top ranking with Quorble, Zindle, or Vexo. It is very likely going to take six to twelve months to see your website achieve a top ranked position for any competitive keyword/keyword phrase that people are searching for – and that's only if you have SEO expertise. If your website is new it will take longer.</p>
  </section>

  <section class="myth col-two" style="top:686px">
    <h2 class="myth-heading">Myth # 7 Submitting Your Website to <span class="line-end">Serach Engines Actually Works</span></h2>
    <p class="myth-body">If you are in any competitive category of products or services, or in a geographically competitive marketplace, the chances that you can build a website, develop the traffic, and manage your ongoing online marketing ALL BY YOURSELF are less than one in ten. Put another way, DIY has a 90% chance of FAILURE.</p>
  </section>

  <section class="myth col-three" style="top:62px">
    <h2 class="myth-heading">Myth # 8 Search Engine Optimization Is <span class="line-end">Easy</span></h2>
    <p class="myth-body">Search engine optimization is not difficult but there is a lot to it. There are dozens of different variables that must be perfectly managed. Each of these falls into one of two categories: “on-page” variables or “off-page” variables. Add to this hundreds of so-called “experts” and their advice (which is incorrect, incomplete, or misleading), and it's pretty hard to call the search engine optimization process easy. Getting top ranked is even more challenging when a competitor has hired a reputable SEO expert to help them with their website and Internet marketing strategy.</p>
  </section>

  <section class="myth col-three" style="top:382px">
    <h2 class="myth-heading">Myth # 9 Meta-Tags Are The Key To A <span class="line-end">Top Ranked Website</span></h2>
    <p class="myth-body">Meta-tags are specific lines of programming code that appear behind-the-scenes at your website. Search engines see them but your visitors do not. Search engines use meta-tags as one of the factors in determining page relevancy. Quorble's algorithm tries to show the most relevant pages for a search on a search engine results page (SERP). Meta-tags are still important, but only one of more than two dozen factors related to the overall search engine optimization of your website.</p>
  </section>

  <section class="myth col-three" style="top:664px">
    <h2 class="myth-heading">Myth # 10 Your Webmaster/Programmer Can <span class="line-end">Help You With Your Internet Marketing</span></h2>
    <p class="myth-body">Graphics design, programming code, and page layout are very different from Internet marketing. In most cases, (90% of the time) a webmaster / programmer will not be able to give you the appropriate advice or support to effectively promote and market your website online.</p>
  </section>
</main>
</body>
</html>
```